Custom text for dubstep artist.

Simple but yet complex

Need a cd cover for "Velvet Ember"
we need the font to look futuristic preferably glass,
glowing red colour, centre of the case, grungy dark / space background
3-4 clean horizontal/slightly angled slashes through the text.
shattering edges on text, glass going outwards.

Refer to other dub step albums on google to get the general idea.
We look forward to see the results!

Target Market(s)

Graphic Designers

Industry/Entity Type

Digital

```html
<!DOCTYPE html>
<html lang="en">
<head>
<meta charset="utf-8">
<title>Velvet Ember – Cover</title>
<link rel="stylesheet" href="https://fonts.googleapis.com/css2?family=Josefin+Sans:wght@600&display=swap">
<style>
  :root {
    --void: #02090b;
    --deep-teal: #0a2629;
    --screen-teal: #0e3a3e;
    --cyan-haze: #7fe6ea;
    --cyan-bright: #d6ffff;
    --ember-red: #ff2410;
    --ember-hot: #ff6a48;
    --ember-core: #ffb39a;
    --shard-light: #f6dcc0;
    --ember-glow: rgba(255, 50, 15, 0.9);
  }
  html, body {
    margin: 0;
    padding: 0;
    width: 1200px;
    height: 1200px;
    overflow: hidden;
    background: var(--void);
  }
  .cover {
    position: relative;
    width: 1200px;
    height: 1200px;
    overflow: hidden;
    background: linear-gradient(160deg, var(--deep-teal) 0%, var(--void) 50%, #0b2c2f 100%);
  }
  .cover__screen {
    position: absolute;
    left: 0;
    top: 0;
    width: 520px;
    height: 1200px;
    background:
      radial-gradient(ellipse 260px 520px at 80px 560px, rgba(40, 130, 136, 0.55), transparent 75%),
      radial-gradient(ellipse 420px 160px at 260px 1080px, rgba(127, 230, 234, 0.45), transparent 70%),
      linear-gradient(90deg, var(--screen-teal), transparent);
  }
  .cover__art {
    position: absolute;
    inset: 0;
    width: 1200px;
    height: 1200px;
  }
  .title-line {
    font-family: "Josefin Sans", sans-serif;
    font-weight: 600;
    fill: url(#emberFill);
    stroke: var(--ember-core);
    stroke-width: 2;
    stroke-linejoin: round;
    paint-order: stroke fill;
    filter: drop-shadow(0 0 5px var(--ember-glow)) drop-shadow(0 0 20px var(--ember-glow));
  }
  .title-line--top { font-size: 440px; }
  .title-line--bottom { font-size: 318px; }
  .slash {
    stroke: var(--cyan-bright);
    stroke-width: 5;
    stroke-linecap: butt;
  }
  .shard { fill: var(--ember-red); }
  .shard--light { fill: var(--shard-light); }
  .shard--hot { fill: var(--ember-hot); }
</style>
</head>
<body>
  <main class="cover">
    <div class="cover__screen" role="img" aria-label="Glowing cyan lines of code on a tilted dark screen"></div>
    <svg class="cover__art" viewBox="0 0 1200 1200" xmlns="http://www.w3.org/2000/svg" aria-label="Velvet Ember">
      <defs>
        <filter id="grainCloud" x="0" y="0" width="100%" height="100%">
          <feTurbulence type="fractalNoise" baseFrequency="0.012 0.02" numOctaves="5" seed="7"/>
          <feColorMatrix values="0 0 0 0 0.62  0 0 0 0 0.95  0 0 0 0 0.96  2.4 0 0 0 -0.9"/>
        </filter>
        <filter id="speckle" x="0" y="0" width="100%" height="100%">
          <feTurbulence type="fractalNoise" baseFrequency="0.9" numOctaves="1" seed="3"/>
          <feColorMatrix values="0 0 0 0 0.85  0 0 0 0 1  0 0 0 0 1  6 0 0 0 -4.6"/>
        </filter>
        <radialGradient id="cloudMaskFill" cx="0.66" cy="0.64" r="0.55">
          <stop offset="0" stop-color="#fff"/>
          <stop offset="0.7" stop-color="#fff" stop-opacity="0.7"/>
          <stop offset="1" stop-color="#fff" stop-opacity="0.15"/>
        </radialGradient>
        <mask id="cloudMask">
          <rect width="1200" height="1200" fill="url(#cloudMaskFill)"/>
        </mask>
        <linearGradient id="emberFill" x1="0" y1="0" x2="0" y2="1">
          <stop offset="0" stop-color="#ff5236"/>
          <stop offset="0.5" stop-color="var(--ember-red)"/>
          <stop offset="1" stop-color="#e81a08"/>
        </linearGradient>
      </defs>

      <g class="backdrop" role="img" aria-label="Grungy dark space smoke in cyan tones">
        <rect width="1200" height="1200" filter="url(#grainCloud)" mask="url(#cloudMask)"/>
        <rect width="1200" height="1200" filter="url(#speckle)" opacity="0.6"/>
      </g>

      <text class="title-line title-line--top" x="40" y="624" textLength="1106" lengthAdjust="spacingAndGlyphs">VELVET</text>
      <text class="title-line title-line--bottom" x="50" y="880" textLength="1090" lengthAdjust="spacingAndGlyphs">EMBER</text>

      <g class="slashes">
        <line class="slash" x1="436" y1="316" x2="336" y2="500"/>
        <line class="slash" x1="760" y1="296" x2="628" y2="566"/>
        <line class="slash" x1="904" y1="398" x2="730" y2="630"/>
        <line class="slash" x1="226" y1="716" x2="146" y2="872"/>
        <line class="slash" x1="612" y1="690" x2="494" y2="888"/>
      </g>

      <g class="shards">
        <polygon class="shard shard--light" points="560,88 610,80 618,104 574,118"/>
        <polygon class="shard" points="566,96 604,90 598,108"/>
        <polygon class="shard shard--light" points="870,124 900,120 896,140 876,140"/>
        <polygon class="shard" points="900,66 916,60 912,78"/>
        <polygon class="shard shard--hot" points="790,106 806,96 802,128"/>
        <polygon class="shard shard--light" points="904,172 924,168 922,184"/>
        <polygon class="shard" points="1020,140 1032,134 1030,152"/>
        <polygon class="shard shard--light" points="760,276 784,270 780,292"/>
        <polygon class="shard" points="960,300 980,290 990,316 968,322"/>
        <polygon class="shard shard--hot" points="1100,240 1112,234 1108,256"/>
        <polygon class="shard shard--light" points="880,312 900,306 902,326"/>
        <polygon class="shard" points="1150,300 1164,296 1160,316"/>
        <polygon class="shard" points="1162,400 1174,396 1176,412"/>
        <polygon class="shard shard--hot" points="1168,460 1182,456 1186,474"/>
        <polygon class="shard" points="1150,520 1166,512 1168,530"/>
        <polygon class="shard shard--light" points="1160,580 1174,578 1170,594"/>
        <polygon class="shard" points="1176,640 1190,632 1194,650"/>
        <polygon class="shard shard--hot" points="1156,700 1170,696 1168,714"/>
        <polygon class="shard" points="1170,760 1186,756 1184,776"/>
        <polygon class="shard" points="1150,840 1166,832 1170,852"/>
        <polygon class="shard shard--light" points="1176,900 1190,896 1188,912"/>
        <polygon class="shard" points="1130,950 1146,944 1150,962"/>
        <polygon class="shard shard--hot" points="1160,1010 1176,1004 1174,1022"/>
        <polygon class="shard" points="1100,1060 1116,1056 1112,1072"/>
        <polygon class="shard" points="840,1030 870,1022 880,1048 850,1062 838,1052"/>
        <polygon class="shard shard--hot" points="844,1040 868,1034 862,1054"/>
        <polygon class="shard" points="760,930 772,924 770,944"/>
        <polygon class="shard" points="960,880 972,876 970,892"/>
        <polygon class="shard shard--light" points="1000,940 1014,934 1012,952"/>
        <polygon class="shard" points="700,1000 712,994 710,1012"/>
        <polygon class="shard" points="620,1060 634,1054 630,1074"/>
        <polygon class="shard shard--hot" points="1050,1110 1064,1104 1062,1122"/>
        <polygon class="shard" points="940,1120 952,1116 950,1132"/>
        <polygon class="shard" points="1120,1140 1132,1136 1130,1152"/>
        <polygon class="shard shard--light" points="700,440 716,434 714,452"/>
        <polygon class="shard" points="760,460 770,454 768,470"/>
        <polygon class="shard" points="680,520 690,514 690,530"/>
        <polygon class="shard shard--hot" points="728,490 738,486 736,500"/>
        <polygon class="shard" points="520,520 534,512 530,532"/>
        <polygon class="shard shard--light" points="470,610 488,604 482,626"/>
        <polygon class="shard" points="300,780 316,774 314,792"/>
        <polygon class="shard" points="420,700 432,694 430,712"/>
        <polygon class="shard shard--light" points="540,690 556,684 552,704"/>
        <polygon class="shard" points="90,330 100,324 98,340"/>
        <polygon class="shard shard--light" points="30,310 44,304 40,322"/>
        <polygon class="shard" points="20,560 32,556 30,572"/>
        <polygon class="shard shard--hot" points="380,860 392,854 390,872"/>
        <polygon class="shard" points="640,160 652,156 648,172"/>
        <polygon class="shard" points="1060,200 1072,196 1068,212"/>
        <polygon class="shard shard--light" points="1200,360 1186,352 1190,372"/>
      </g>
    </svg>
  </main>
</body>
</html>
```